Business Card Design Project

Business Card
We are rebranding with a new logo
Industry/Entity Type
Business
Contact Information for Business Card
Dennis Morvale +61 487215963 dennis@quorv.com.au P.O. Box 872 Fernlow QLD 4309
Requirements
Must have
- Logo

```html
<!DOCTYPE html>
<html lang="en">
<head>
<meta charset="utf-8">
<title>Quorv International – Business Card</title>
<link href="https://fonts.googleapis.com/css2?family=Dancing+Script:wght@600&family=Roboto:wght@400;700&display=swap" rel="stylesheet">
<style>
  :root {
    --page-bg: #d8d5d1;
    --card-bg: #eef0ef;
    --ink: #1f2a30;
    --name-teal: #1b5866;
    --brand-orange: #e2621f;
    --brand-teal: #1a6f8a;
    --brand-teal-deep: #14556b;
    --band-text: #d9e6ea;
  }
  html, body {
    margin: 0;
    padding: 0;
    width: 1200px;
    height: 1010px;
    overflow: hidden;
    background: var(--page-bg);
  }
  .canvas {
    position: relative;
    width: 1200px;
    height: 1010px;
  }
  .card {
    position: absolute;
    left: 80px;
    top: 204px;
    width: 1040px;
    height: 602px;
    background: var(--card-bg);
    box-shadow: 0 10px 30px rgba(0,0,0,0.12);
    overflow: hidden;
  }
  .brand {
    position: absolute;
    left: 82px;
    top: 120px;
    color: var(--ink);
    font-family: "Roboto", sans-serif;
    font-weight: 700;
    line-height: 1;
  }
  .brand-name {
    display: block;
    font-size: 96px;
    letter-spacing: 1px;
  }
  .brand-line {
    display: block;
    margin-top: 16px;
    font-size: 27px;
    letter-spacing: 4px;
  }
  .person-name {
    position: absolute;
    left: 507px;
    top: 300px;
    margin: 0;
    font-family: "Dancing Script", cursive;
    font-weight: 600;
    font-size: 46px;
    color: var(--name-teal);
  }
  .contact-list {
    position: absolute;
    left: 518px;
    top: 374px;
    margin: 0;
    padding: 0;
    list-style: none;
    font-family: "Roboto", sans-serif;
    font-size: 24px;
    color: var(--ink);
  }
  .contact-item {
    display: flex;
    align-items: center;
    height: 34px;
  }
  .contact-icon {
    width: 22px;
    height: 22px;
    margin-right: 20px;
    fill: var(--brand-orange);
  }
  .footer-bands {
    position: absolute;
    left: 0;
    bottom: 0;
    width: 1040px;
    height: 76px;
  }
  .website {
    position: absolute;
    left: 514px;
    top: 548px;
    font-family: "Roboto", sans-serif;
    font-size: 24px;
    color: var(--band-text);
  }
</style>
</head>
<body>
<div class="canvas">
  <div class="card">
    <div class="brand">
      <span class="brand-name">Quorv</span>
      <span class="brand-line">INTERNATIONAL</span>
    </div>

    <h1 class="person-name">Dennis Morvale</h1>

    <ul class="contact-list">
      <li class="contact-item">
        <svg class="contact-icon" viewBox="0 0 24 24" aria-hidden="true"><path d="M3 7c0-2 2-4 9-4s9 2 9 4v2h-5V7H8v2H3z"/><path d="M6 11h12l2 9H4z"/><circle cx="12" cy="15" r="2.2" fill="var(--card-bg)"/></svg>
        <span>+61 487215963</span>
      </li>
      <li class="contact-item">
        <svg class="contact-icon" viewBox="0 0 24 24" aria-hidden="true"><path d="M2 5h20v14H2z"/><path d="M2 5l10 8 10-8" fill="none" stroke="var(--card-bg)" stroke-width="2"/></svg>
        <span>dennis@quorv.com.au</span>
      </li>
      <li class="contact-item">
        <svg class="contact-icon" viewBox="0 0 24 24" aria-hidden="true"><path d="M12 1a8 8 0 0 0-8 8c0 6 8 14 8 14s8-8 8-14a8 8 0 0 0-8-8z"/><circle cx="12" cy="9" r="3" fill="var(--card-bg)"/></svg>
        <span>P.O. Box 872 Fernlow QLD 4309</span>
      </li>
    </ul>

    <svg class="footer-bands" viewBox="0 0 1040 76" aria-hidden="true">
      <defs>
        <linearGradient id="tealBand" x1="0" y1="0" x2="1" y2="0">
          <stop offset="0" stop-color="var(--brand-teal-deep)"/>
          <stop offset="1" stop-color="var(--brand-teal)"/>
        </linearGradient>
      </defs>
      <rect x="0" y="42" width="470" height="34" fill="var(--brand-orange)"/>
      <polygon points="463,0 1040,0 1040,76 429,76" fill="url(#tealBand)"/>
    </svg>
    <div class="website">www.quorv.com.au</div>
  </div>
</div>
</body>
</html>
```